eBook cover and content: Steering Teams With Quiet Courage

I teach a leadership program to companies that was developed at Varnelo and now need an eBook cover and content design. This downloadable eBook will be offered online in exchange for prospects' contact details. It needs to be designed with a sophisticated, senior HR executive audience in mind. There are some assets that are available for you to work with including photographs, a logo device for the program, and a colour palette (same as Varnelo's blue, green, yellow and red). Note that while the program was developed at Varnelo it is NOT a Varnelo product and I need to ensure that the eBook does not breach license guidelines. I have attached a very rough mockup of the content, images and graphic elements to help.

Target Market(s)

Senior business leaders and HR professionals.

Industry/Entity Type

Leadership

Font styles to use
Sans Serif

Requirements
Must have
• Keep it simple. Clean, contemporary, professional feel. This is a high-value decision for a company and needs to look modern, progressive and credible. Downloadable PDF. Easy to read and digest layout.
• Colours - see attached screenshot for red, blue, green, yellow ref. Additionally charcoal for most type and purple 330033 as extra colour is okay.
• Landscape format please.
Nice to have
• Plenty of white space.

```html
<!DOCTYPE html>
<html lang="en">
<head>
<meta charset="utf-8">
<title>Three Ways to Build Better Leadership — eBook spreads</title>
<link rel="stylesheet" href="https://fonts.googleapis.com/css2?family=Roboto:wght@300;400;500&display=swap">
<style>
  :root {
    --backdrop: #0b9f4b;
    --brand-green: #1a9a52;
    --brand-green-soft: #d9efe1;
    --brand-green-pale: #eef7f1;
    --brand-green-mid: #dcefe3;
    --charcoal: #4a4a4a;
    --charcoal-light: #666666;
    --page: #ffffff;
  }
  * { margin: 0; padding: 0; box-sizing: border-box; }
  html, body { width: 1200px; height: 874px; overflow: hidden; }
  body {
    background: var(--backdrop);
    font-family: "Roboto", Arial, sans-serif;
    font-weight: 300;
    color: var(--charcoal);
    position: relative;
  }
  .page {
    position: absolute;
    width: 572px;
    height: 397px;
    background: var(--page);
    overflow: hidden;
  }
  .page--cover { left: 16px; top: 24px; }
  .page--four  { left: 610px; top: 24px; }
  .page--three { left: 16px; top: 449px; }
  .page--five  { left: 610px; top: 449px; }

  /* cover */
  .cover-photo {
    position: absolute; inset: 0;
    background:
      radial-gradient(ellipse at 60% 12%, #f4eef3 0%, #e9dde6 35%, transparent 60%),
      radial-gradient(ellipse at 58% 62%, #6f5a4c 0%, transparent 35%),
      radial-gradient(ellipse at 20% 75%, #b89a88 0%, transparent 40%),
      radial-gradient(ellipse at 85% 80%, #8d7a86 0%, transparent 45%),
      linear-gradient(180deg, #efe6ee 0%, #cdb9c6 45%, #7d6a6c 100%);
  }
  .cover-title {
    position: absolute; left: 19px; top: 60px;
    font-size: 19px; line-height: 22px; font-weight: 400;
    color: var(--brand-green); letter-spacing: 0.2px;
  }
  .cover-rule {
    position: absolute; left: 19px; top: 134px;
    width: 60px; height: 3px; background: var(--brand-green);
  }

  /* running header */
  .running-head {
    position: absolute; left: 20px; top: 21px;
    display: flex; align-items: center; gap: 5px;
    font-size: 7px; font-weight: 400; color: var(--charcoal);
  }
  .running-head__mark {
    width: 7px; height: 7px; border-radius: 50%; background: var(--brand-green);
  }

  /* section heading */
  .section-title {
    position: absolute; left: 20px;
    display: flex; align-items: flex-start; gap: 4px;
    font-size: 15px; line-height: 18px; color: var(--brand-green); font-weight: 300;
  }
  .section-title__num {
    flex: none; width: 17px; height: 17px; border-radius: 50%;
    background: var(--brand-green-soft); color: var(--brand-green);
    font-size: 13px; line-height: 17px; text-align: center;
  }

  /* body copy */
  .body-copy {
    position: absolute; left: 200px; width: 340px;
    font-size: 8.4px; line-height: 10.5px; color: var(--charcoal-light);
  }
  .body-copy p { margin-bottom: 6px; }
  .body-copy strong { font-weight: 500; color: var(--charcoal); }

  .folio {
    position: absolute; right: 0; bottom: 12px;
    display: flex; align-items: center; gap: 3px;
    font-size: 7px; color: var(--charcoal);
  }
  .folio::after {
    content: ""; width: 6px; height: 11px; background: var(--brand-green);
  }

  /* leadership model diagram */
  .model {
    position: absolute; left: 200px; top: 236px; width: 346px; height: 62px;
  }
  .model text { font-family: "Roboto", Arial, sans-serif; }

  /* figure panel */
  .brain-figure {
    position: absolute; left: 200px; top: 213px; width: 342px; height: 74px;
    background: var(--brand-green-pale);
  }
  .brain-figure__image {
    position: absolute; left: 20px; right: 20px; top: 6px; height: 50px;
    background: linear-gradient(90deg, var(--brand-green-pale) 0%, var(--brand-green-mid) 50%, var(--brand-green-pale) 100%);
  }
  .brain-figure__caption {
    position: absolute; left: 0; right: 0; bottom: 7px; text-align: center;
    font-size: 4.5px; color: var(--brand-green); font-weight: 400;
  }
</style>
</head>
<body>

  <!-- Cover -->
  <section class="page page--cover">
    <div class="cover-photo" role="img" aria-label="Photograph of smiling people mingling at a leadership workshop event"></div>
    <h1 class="cover-title">THREE WAYS TO<br>BUILD BETTER<br>LEADERSHIP</h1>
    <div class="cover-rule"></div>
  </section>

  <!-- Page 4 -->
  <section class="page page--four">
    <div class="running-head"><span class="running-head__mark"></span>Steady Within</div>
    <h2 class="section-title" style="top:64px"><span class="section-title__num">2</span><span>Learning to lead in<br>interesting times</span></h2>
    <div class="body-copy" style="top:64px">
      <p>“May you live in interesting times” is known as the “Chinese Curse”. It’s a curse because “interesting” is a proxy for change, chaos and conflict.</p>
      <p>Like it or not, we’re all living in interesting times.</p>
      <p>Command and control. Carrots and sticks. Not much about “top down” leadership models work now, if they ever did. You need new skills to adapt and thrive.</p>
      <p>High-performing companies are flatter, faster, and more agile than their predecessors.</p>
      <p>So you’ll need a different model for leadership. It’s no longer about exercising your authority, it’s about developing your influence.</p>
      <p>Think about that for a moment.</p>
      <p>Your influence is determined by the way you behave. Your behaviour is tied directly to your emotional intelligence. Which means building new leadership ‘muscles’ starts with training your peoples’ EQ.</p>
    </div>
    <svg class="model" viewBox="0 0 346 62" aria-label="Traditional top-down leadership compared with transformational inside-out leadership">
      <text x="6" y="12" font-size="6" fill="#1a9a52" font-weight="500">Traditional leadership</text>
      <text x="6" y="19" font-size="6" fill="#1a9a52" font-weight="500">“Top down”</text>
      <polygon points="101,4 72,58 130,58" fill="#d9efe1"/>
      <line x1="93" y1="2" x2="65" y2="56" stroke="#9fcfb0" stroke-width="0.6"/>
      <line x1="109" y1="2" x2="137" y2="56" stroke="#9fcfb0" stroke-width="0.6"/>
      <line x1="88" y1="28" x2="114" y2="28" stroke="#fff" stroke-width="0.6"/>
      <line x1="80" y1="44" x2="122" y2="44" stroke="#fff" stroke-width="0.6"/>
      <text x="101" y="22" font-size="5" fill="#1a9a52" text-anchor="middle">CEO</text>
      <text x="101" y="38" font-size="5" fill="#1a9a52" text-anchor="middle">Management</text>
      <text x="101" y="54" font-size="5" fill="#1a9a52" text-anchor="middle">Minions</text>
      <text x="160" y="12" font-size="6" fill="#1a9a52" font-weight="500">Transformational</text>
      <text x="160" y="19" font-size="6" fill="#1a9a52" font-weight="500">leadership “Inside out”</text>
      <line x1="286" y1="0" x2="286" y2="62" stroke="#9fcfb0" stroke-width="0.6"/>
      <line x1="254" y1="31" x2="318" y2="31" stroke="#9fcfb0" stroke-width="0.6"/>
      <circle cx="286" cy="31" r="28" fill="#d9efe1"/>
      <circle cx="286" cy="31" r="19" fill="#bfe3cb"/>
      <circle cx="286" cy="31" r="10" fill="#9fd4b1"/>
      <text x="286" y="9" font-size="4.5" fill="#1a9a52" text-anchor="middle">Influence</text>
      <text x="286" y="17" font-size="4.5" fill="#1a9a52" text-anchor="middle">Behaviour</text>
      <text x="286" y="33" font-size="5" fill="#1a9a52" text-anchor="middle">EQ</text>
    </svg>
    <div class="body-copy" style="top:311px">
      <p>Make sure leadership training provides your people with a leadership model for now, and the skills they need to muscle-up on emotional intelligence.</p>
      <p>And now, to number three.</p>
    </div>
    <div class="folio">4</div>
  </section>

  <!-- Page 3 -->
  <section class="page page--three">
    <div class="running-head"><span class="running-head__mark"></span>Steady Within</div>
    <h2 class="section-title" style="top:64px"><span class="section-title__num">1</span><span>Getting off autopilot</span></h2>
    <div class="body-copy" style="top:65px">
      <p>We’re all running on autopilot.</p>
      <p>You know what I mean. Days, weeks, sometimes even months go by and we haven’t been present or paying attention. Have you ever driven somewhere only to arrive and not remember how you actually got there? Or been five pages into a book and not remembered a word?</p>
      <p>Running on autopilot has become the new normal for many of us.</p>
      <p>This is what it feels like:</p>
      <p><strong>Your attention is in the past or future.</strong> You’re ruminating about things that have already happened, or your worrying about things that might happen. Either way, you’re not present.</p>
      <p><strong>You’re distracted.</strong> Easily and all the time. Probably more often than a Goldfish.</p>
      <p><strong>You’re reactive or judgmental.</strong> Instead of accepting situations as they are and working with them, you’re getting caught up in your head. You lose connection with who you are, who you’re with and what you’re doing.</p>
      <p><strong>You’re acting based on habits, patterns and assumptions.</strong> We often default to old ways of thinking and behaviours, and typical ways of reacting. But wouldn’t it be better to have an open mind and consider your responses more deeply?</p>
      <p>So the first and most important challenge for leadership development is to help people get off autopilot, and stay off.</p>
    </div>
    <div class="folio">3</div>
  </section>

  <!-- Page 5 -->
  <section class="page page--five">
    <div class="running-head"><span class="running-head__mark"></span>Steady Within</div>
    <h2 class="section-title" style="top:64px"><span class="section-title__num">3</span><span>Changing your mind<br>to change your brain</span></h2>
    <div class="body-copy" style="top:64px">
      <p>Emotional intelligence is what separates star performers from the also rans. It’s also the stuff of outstanding leadership. And wellbeing. Especially now.</p>
      <p>But most people think that their EQ is fixed, like those funny toes you got from your parents.</p>
      <p>What they don’t realise that your brain is ‘plastic’ and can be rewired and reshaped, until you’re at least 90. So you’ve got time.</p>
      <p>Just make sure you’re changing your brain in ways that will be helpful for this crazy-busy world of ours.</p>
      <p>You’ll need to switch off the Default Mode Network of your brain. Not easy when you have so much going on in there. In default mode our brain is lit up like a Christmas tree. You don’t need any more lights and baubles, you need less.</p>
    </div>
    <figure class="brain-figure">
      <div class="brain-figure__image" role="img" aria-label="Labelled illustration of a brain with the default mode network regions highlighted"></div>
      <figcaption class="brain-figure__caption">Your brain with the Default Mode Network “On”. Halden et al 2011; image from Morvaine et al 2014.</figcaption>
    </figure>
    <div class="body-copy" style="top:297px">
      <p>Leadership programs need to be helping you rewire your brain for calm and clarity, and to help make you more agile, more adaptable and more open and available for critical thinking, collaboration, creativity and problem solving.</p>
      <p>Because they’re the skills you need to lead and contribute at your best.</p>
    </div>
    <div class="folio">5</div>
  </section>

</body>
</html>
```